Website Design - TallyPorchHelpers.net

PLEASE CHECK WORD DOCUMENT ATTACHED FOR WEBSITE FLOW.

Target Market(s)

REAL ESTATE AGENTS ARE THE TARGET MARKET

Industry/Entity Type

Real Estate

Coding

Coded - Design and coding required

Number of Pages Required

4 page

Colors

Designer to choose colors to be used in the design.

Requirements
Must have
• WE LIKE RED LOGO ATTACHED
Nice to have
• PLEASE CHECK WORD DOCUMENT ATTACHED FOR WEBSITE FLOW.
Should not have

```html
<!DOCTYPE html>
<html lang="en">
<head>
<meta charset="utf-8">
<title>TallyPorchHelpers.net</title>
<link rel="stylesheet" href="https://fonts.googleapis.com/css2?family=Poppins:wght@400;500;600;700&family=Open+Sans:wght@400;600;700&display=swap">
<style>
:root{
  --red:#e8121f;
  --red-dark:#c40c17;
  --navy:#25306e;
  --navy-deep:#1d2660;
  --purple:#5a2d82;
  --ink:#2b2b33;
  --muted:#6d6f7a;
  --line:#e2e3e8;
  --paper:#f3f3f5;
  --white:#ffffff;
}
*{box-sizing:border-box;margin:0;padding:0}
html,body{width:1200px;height:4762px;overflow:hidden}
body{font-family:"Open Sans",Arial,sans-serif;color:var(--ink);background:var(--white);position:relative}
h1,h2,h3,h4,.btn,.nav a{font-family:"Poppins",Arial,sans-serif}
.section{position:absolute;left:0;width:1200px}
.btn-red{display:inline-block;background:var(--red);color:var(--white);font-family:"Poppins",Arial,sans-serif;font-weight:600;font-size:13px;letter-spacing:.4px;padding:11px 22px;border-radius:3px;text-transform:uppercase}
.cta-row{position:absolute;left:0;width:1200px;text-align:center}
.section-title{position:absolute;left:0;width:1200px;text-align:center;font-size:22px;font-weight:600}

/* header */
.site-header{top:0;height:80px;background:var(--white);box-shadow:0 1px 4px rgba(0,0,0,.08);z-index:2}
.brand{position:absolute;left:238px;top:24px;display:flex;align-items:center;gap:8px}
.brand-mark{width:28px;height:28px;background:var(--red)}
.brand-name{font-family:"Poppins",Arial,sans-serif;font-weight:700;font-size:14px;color:var(--red);line-height:1.05;width:90px}
.nav{position:absolute;left:385px;top:33px;display:flex;gap:24px;align-items:center}
.nav a{font-size:11px;font-weight:600;color:var(--ink);text-decoration:none;text-transform:uppercase}
.call{position:absolute;left:845px;top:26px;display:flex;align-items:center;gap:6px}
.call-label{font-size:9px;color:var(--muted);display:block}
.call-number{font-size:13px;font-weight:700;color:var(--red);font-family:"Poppins",Arial,sans-serif}

/* hero */
.hero{top:80px;height:523px}
.hero-photo{position:absolute;inset:0;background:linear-gradient(120deg,#d9c9b2 0%,#a98f74 40%,#6f5c4f 70%,#3b3335 100%)}
.hero-shade{position:absolute;inset:0;background:rgba(20,20,30,.25)}
.hero-copy{position:absolute;top:215px;left:0;width:1200px;text-align:center;color:var(--white)}
.hero-copy h1{font-size:30px;font-weight:700}
.hero-copy p{font-size:17px;font-weight:600;margin-top:4px;line-height:1.35}

/* options */
.options{top:603px;height:357px}
.options-band{position:absolute;top:0;left:0;width:1200px;height:229px;background:linear-gradient(180deg,var(--red) 0%,var(--red-dark) 100%)}
.options .section-title{top:42px;color:var(--white);font-size:20px}
.option-cards{position:absolute;top:102px;left:232px;width:736px;display:flex;gap:22px}
.option-card{flex:1;height:146px;background:var(--white);box-shadow:0 6px 16px rgba(0,0,0,.18);text-align:center;position:relative;padding-top:30px}
.option-card svg{display:block;margin:0 auto 12px}
.option-card h3{font-size:12px;font-weight:600;line-height:1.35;text-transform:uppercase}
.option-card::after{content:"";position:absolute;left:0;bottom:0;width:100%;height:8px;background:linear-gradient(90deg,var(--navy) 0 50%,var(--red) 50% 100%)}
.options .cta-row{top:290px}

/* how */
.how{top:960px;height:399px}
.how .section-title{top:40px}
.steps{position:absolute;top:105px;left:250px;width:700px;display:flex;justify-content:space-between}
.step{width:200px;text-align:center}
.step-num{width:40px;height:40px;border-radius:50%;background:var(--navy);color:var(--white);font-family:"Poppins",Arial,sans-serif;font-size:12px;font-weight:600;line-height:40px;margin:0 auto 14px;box-shadow:0 0 0 5px #dfe1ef}
.step p{font-size:11.5px;color:var(--muted);line-height:1.6}
.step-arrow{position:absolute;top:124px}
.how .cta-row{top:280px}

/* packages */
.packages{top:1359px;height:673px;background:var(--paper)}
.packages .section-title{top:52px}
.plans{position:absolute;top:108px;left:232px;width:736px;display:flex;gap:9px}
.plan{flex:1;background:var(--white);box-shadow:0 2px 8px rgba(0,0,0,.08);height:438px;position:relative;text-align:center}
.plan-head{height:44px;background:#eceef2;font-family:"Poppins",Arial,sans-serif;font-weight:600;font-size:12px;line-height:44px;color:var(--ink)}
.plan.featured .plan-head{background:var(--navy);color:var(--white)}
.plan-price{width:56px;height:56px;border-radius:50%;background:var(--red);color:var(--white);margin:-14px auto 10px;font-family:"Poppins",Arial,sans-serif;font-weight:700;font-size:16px;line-height:48px;border:4px solid var(--white)}
.plan.featured .plan-price{background:var(--navy)}
.plan ul{list-style:none;text-align:left;padding:0 12px}
.plan li{font-size:10px;line-height:1.45;color:var(--muted);padding-left:14px;position:relative;margin-bottom:9px}
.plan li::before{content:"";position:absolute;left:0;top:3px;width:7px;height:4px;border-left:2px solid var(--red);border-bottom:2px solid var(--red);transform:rotate(-45deg)}
.plan-btn{display:block;margin:6px 12px 10px;background:var(--navy);color:var(--white);font-family:"Poppins",Arial,sans-serif;font-size:10px;font-weight:600;padding:9px 0;text-transform:uppercase}
.plan.featured .plan-btn{background:var(--red)}
.plan-note{font-size:8.5px;color:var(--muted);padding:0 12px;line-height:1.4}
.packages .cta-row{top:583px}

/* marketing */
.marketing{top:2032px;height:619px;background:linear-gradient(135deg,var(--purple) 0%,#43307f 45%,var(--navy) 100%);overflow:hidden}
.marketing h2{position:absolute;left:232px;top:68px;color:var(--white);font-size:20px;font-weight:600}
.services{position:absolute;left:232px;top:120px;width:470px;display:grid;grid-template-columns:1fr 1fr;gap:26px 30px}
.service-head{display:flex;align-items:center;gap:9px;color:var(--white);font-family:"Poppins",Arial,sans-serif;font-weight:600;font-size:13px;text-transform:uppercase;margin-bottom:8px}
.service-icon{width:30px;height:30px;border-radius:50%;border:2px solid var(--white);display:flex;align-items:center;justify-content:center}
.service p{font-size:10.5px;line-height:1.55;color:#d8d6ea}
.marketing .btn-red{position:absolute;left:232px;top:515px}
.agent-photo{position:absolute;left:740px;top:150px;width:300px;height:469px;background:linear-gradient(180deg,#cfc7d6 0%,#9c92b3 55%,#584f80 100%);opacity:.9}

/* service area */
.area{top:2651px;height:667px}
.area-band{position:absolute;top:0;left:0;width:1200px;height:153px;background:linear-gradient(180deg,#3a2f7e 0%,var(--navy) 100%)}
.area .section-title{top:40px;color:var(--white)}
.search{position:absolute;left:360px;top:95px;display:flex}
.search-input{width:380px;height:34px;background:var(--white);font-size:11px;color:#9a9ba5;padding:9px 14px}
.search-btn{width:92px;height:34px;background:var(--red);color:var(--white);font-family:"Poppins",Arial,sans-serif;font-weight:600;font-size:11px;text-align:center;line-height:34px;text-transform:uppercase}
.map{position:absolute;top:153px;left:0;width:1200px;height:428px;background:linear-gradient(160deg,#e9ebe4 0%,#dfe3d8 45%,#abd0e6 70%,#9fc8e1 100%)}
.area .cta-row{top:604px}

/* faq */
.faq{top:3318px;height:524px;background:linear-gradient(135deg,var(--purple) 0%,#3c2f7d 50%,var(--navy) 100%)}
.faq .section-title{top:62px;color:var(--white)}
.faq-cols{position:absolute;top:122px;left:232px;width:736px;display:flex;gap:28px}
.faq-col{flex:1}
.faq-item{background:var(--white);height:32px;margin-bottom:10px;display:flex;justify-content:space-between;align-items:center;padding:0 12px;font-size:11px;font-weight:600;color:var(--ink)}
.faq-item span:last-child{font-size:15px;color:var(--navy)}
.faq-item.open{background:var(--red);color:var(--white);margin-bottom:0}
.faq-item.open span:last-child{color:var(--white)}
.faq-answer{background:var(--white);padding:12px 14px;font-size:10.5px;line-height:1.6;color:var(--muted);margin-bottom:10px}
.faq .cta-row{top:426px}

/* testimonials */
.testimonials{top:3842px;height:562px}
.testimonials .section-title{top:56px}
.quotes{position:absolute;top:118px;left:232px;width:736px;display:flex;gap:44px}
.quote{flex:1;text-align:center;position:relative;padding:0 18px}
.quote-mark{position:absolute;top:-6px;font-family:"Poppins",Arial,sans-serif;font-size:40px;color:var(--red);line-height:1}
.quote-mark.l{left:-6px}
.quote-mark.r{right:-6px}
.quote p{font-size:11.5px;line-height:1.7;color:var(--muted)}
.avatar{width:52px;height:52px;border-radius:50%;background:linear-gradient(135deg,#d7c6b8,#8e7a70);margin:20px auto 8px}
.quote h4{font-size:15px;font-weight:500;color:var(--ink)}
.quote-divider{width:1px;background:var(--line)}
.dots{position:absolute;top:410px;left:0;width:1200px;display:flex;justify-content:center;gap:7px}
.dots i{width:7px;height:7px;border-radius:50%;background:#d6d7de}
.dots i.on{background:var(--red)}
.testimonials .cta-row{top:448px}

/* footer */
.site-footer{top:4404px;height:358px;background:var(--navy-deep);border-top:4px solid var(--red)}
.ribbon{position:absolute;top:-18px;left:440px;width:320px;height:36px;background:var(--red);color:var(--white);font-family:"Poppins",Arial,sans-serif;font-weight:600;font-size:12px;text-align:center;line-height:36px;text-transform:uppercase;border-radius:18px}
.footer-cols{position:absolute;top:56px;left:232px;width:736px;display:flex;gap:22px}
.footer-col{color:#c9cce0;font-size:9.5px;line-height:1.7}
.footer-col h4{font-size:10px;color:var(--white);font-weight:600;text-transform:uppercase;margin-bottom:8px}
.footer-col.about{width:200px}
.footer-col.contact{width:160px}
.footer-col.links{width:110px}
.footer-col.form{width:200px}
.socials{display:flex;gap:6px;margin-top:10px}
.socials i{width:20px;height:20px;border-radius:50%;border:1px solid #c9cce0}
.field{height:22px;background:var(--white);margin-bottom:6px;font-size:9px;color:#9a9ba5;padding:4px 8px}
.send{height:24px;background:var(--red);color:var(--white);font-family:"Poppins",Arial,sans-serif;font-weight:600;font-size:9px;text-align:center;line-height:24px;text-transform:uppercase}
.bottom-bar{position:absolute;bottom:0;left:0;width:1200px;height:31px;background:#151c4c;color:#aeb2cc;font-size:9px;line-height:31px}
.bottom-bar .copy{position:absolute;left:232px}
.bottom-bar .legal{position:absolute;right:232px}
</style>
</head>
<body>

<header class="section site-header">
  <div class="brand"><span class="brand-mark"></span><span class="brand-name">TallyPorch Helpers</span></div>
  <nav class="nav">
    <a>How it works</a><a>Service area</a><a>Pricing</a><a>About us</a><a>FAQ</a>
    <svg width="12" height="12" viewBox="0 0 12 12"><circle cx="5" cy="5" r="3.8" fill="none" stroke="#2b2b33" stroke-width="1.5"/><line x1="8" y1="8" x2="11" y2="11" stroke="#2b2b33" stroke-width="1.5"/></svg>
  </nav>
  <div class="call">
    <svg width="18" height="18" viewBox="0 0 24 24"><path d="M6.6 10.8a15 15 0 0 0 6.6 6.6l2.2-2.2a1 1 0 0 1 1-.25 11.4 11.4 0 0 0 3.6.57 1 1 0 0 1 1 1V20a1 1 0 0 1-1 1A17 17 0 0 1 3 4a1 1 0 0 1 1-1h3.5a1 1 0 0 1 1 1c0 1.25.2 2.45.57 3.57a1 1 0 0 1-.25 1z" fill="#e8121f"/></svg>
    <div><span class="call-label">Click to call us</span><span class="call-number">1-555-014-2290</span></div>
  </div>
</header>

<section class="section hero">
  <div class="hero-photo" role="img" aria-label="Photo of a real estate agent welcoming a couple into a bright home at an open house"></div>
  <div class="hero-shade"></div>
  <div class="hero-copy">
    <h1>Helping agents save time and money.</h1>
    <p>We place signs and boost foot traffic to your open houses<br>using proven marketing techniques.</p>
  </div>
</section>

<section class="section options">
  <div class="options-band"></div>
  <h2 class="section-title">Choose The Option Below That Best Describes You</h2>
  <div class="option-cards">
    <div class="option-card">
      <svg width="30" height="28" viewBox="0 0 30 28"><rect x="3" y="4" width="24" height="22" fill="none" stroke="#e8121f" stroke-width="2"/><rect x="8" y="9" width="4" height="4" fill="#e8121f"/><rect x="18" y="9" width="4" height="4" fill="#e8121f"/><rect x="8" y="16" width="4" height="4" fill="#e8121f"/><rect x="18" y="16" width="4" height="4" fill="#e8121f"/><rect x="13" y="20" width="4" height="6" fill="#e8121f"/></svg>
      <h3>I'm a<br>full on brokerage</h3>
    </div>
    <div class="option-card">
      <svg width="34" height="28" viewBox="0 0 34 28"><circle cx="17" cy="8" r="5" fill="#e8121f"/><circle cx="7" cy="11" r="4" fill="#e8121f"/><circle cx="27" cy="11" r="4" fill="#e8121f"/><path d="M9 26c0-6 4-10 8-10s8 4 8 10z" fill="#e8121f"/><path d="M1 26c0-5 3-8 6-8s4 2 4 2l-2 6z" fill="#e8121f"/><path d="M33 26c0-5-3-8-6-8s-4 2-4 2l2 6z" fill="#e8121f"/></svg>
      <h3>I'm an<br>ind. broker with a team</h3>
    </div>
    <div class="option-card">
      <svg width="30" height="28" viewBox="0 0 30 28"><rect x="4" y="2" width="3" height="25" fill="#e8121f"/><rect x="4" y="4" width="22" height="3" fill="#e8121f"/><rect x="11" y="10" width="15" height="10" fill="none" stroke="#e8121f" stroke-width="2"/><line x1="14" y1="7" x2="14" y2="10" stroke="#e8121f" stroke-width="1.5"/><line x1="23" y1="7" x2="23" y2="10" stroke="#e8121f" stroke-width="1.5"/></svg>
      <h3>I need<br>sign placement ASAP</h3>
    </div>
  </div>
  <div class="cta-row"><span class="btn-red">Contact us right now</span></div>
</section>

<section class="section how">
  <h2 class="section-title">How It Works</h2>
  <svg class="step-arrow" style="left:392px" width="120" height="10" viewBox="0 0 120 10"><line x1="0" y1="5" x2="112" y2="5" stroke="#25306e" stroke-width="1.5"/><path d="M112 1l6 4-6 4z" fill="#25306e"/></svg>
  <svg class="step-arrow" style="left:642px" width="120" height="10" viewBox="0 0 120 10"><line x1="0" y1="5" x2="112" y2="5" stroke="#25306e" stroke-width="1.5"/><path d="M112 1l6 4-6 4z" fill="#25306e"/></svg>
  <div class="steps">
    <div class="step"><div class="step-num">01</div><p>We boost foot traffic to your open house using proven marketing channels: social feed ads, SMS notifications, voice broadcasts and email notifications</p></div>
    <div class="step"><div class="step-num">02</div><p>We place open house signs strategically in the surrounding area</p></div>
    <div class="step"><div class="step-num">03</div><p>Store custom signs for you if needed</p></div>
  </div>
  <div class="cta-row"><span class="btn-red">Contact us right now</span></div>
</section>

<section class="section packages">
  <h2 class="section-title">Choose Your Package</h2>
  <div class="plans">
    <div class="plan"><div class="plan-head">5 SIGNS</div><div class="plan-price">$49</div>
      <ul><li>Place signs strategically in both areas according to where the open house is located</li><li>Pick up the signs after the open house</li><li>Store custom signs for you if needed</li></ul>
      <span class="plan-btn">Sign up</span><p class="plan-note">Sign up for a subscription and get these as a monthly plan option</p></div>
    <div class="plan"><div class="plan-head">10 SIGNS</div><div class="plan-price">$59</div>
      <ul><li>Place signs strategically in both areas according to where the open house is located</li><li>Pick up the signs after the open house</li><li>Store custom signs for you if needed</li></ul>
      <span class="plan-btn">Sign up</span><p class="plan-note">Sign up for a subscription and get these as a monthly plan option</p></div>
    <div class="plan featured"><div class="plan-head">15 SIGNS</div><div class="plan-price">$69</div>
      <ul><li>Place signs strategically in both areas according to where the open house is located</li><li>Pick up the signs after the open house</li><li>Store custom signs for you if needed</li></ul>
      <span class="plan-btn">Sign up</span><p class="plan-note">Sign up for a subscription and get these as a monthly plan option</p></div>
    <div class="plan"><div class="plan-head">20 SIGNS</div><div class="plan-price">$79</div>
      <ul><li>Place signs strategically in both areas according to where the open house is located</li><li>Pick up the signs after the open house</li><li>Store custom signs for you if needed</li></ul>
      <span class="plan-btn">Sign up</span><p class="plan-note">Sign up for a subscription and get these as a monthly plan option</p></div>
    <div class="plan"><div class="plan-head">25+ SIGNS</div><div class="plan-price">$</div>
      <ul><li>Place signs strategically in both areas according to where the open house is located</li><li>Pick up the signs after the open house</li><li>Store custom signs for you if needed</li></ul>
      <span class="plan-btn">Click here to create a quote</span><p class="plan-note">Sign up for a subscription and get these as a monthly plan option</p></div>
  </div>
  <div class="cta-row"><span class="btn-red">Contact us right now</span></div>
</section>

<section class="section marketing">
  <h2>Marketing Services</h2>
  <div class="services">
    <div class="service"><div class="service-head"><span class="service-icon"><svg width="14" height="12" viewBox="0 0 14 12"><path d="M1 1h12v8H5l-3 2V9H1z" fill="none" stroke="#fff" stroke-width="1.3"/></svg></span>SMS</div>
      <p>We will send a text message to all the people that lived in the surrounding area of your open house so they know there is a house for sale in their neighborhood and want to see it.</p></div>
    <div class="service"><div class="service-head"><span class="service-icon"><svg width="14" height="10" viewBox="0 0 14 10"><rect x="1" y="1" width="12" height="8" fill="none" stroke="#fff" stroke-width="1.3"/><path d="M1 1l6 5 6-5" fill="none" stroke="#fff" stroke-width="1.3"/></svg></span>Email</div>
      <p>We will send an email message to all the people that lived in the surrounding area of your open house so they know there is a house for sale and want to come check it out.</p></div>
    <div class="service"><div class="service-head"><span class="service-icon"><svg width="12" height="12" viewBox="0 0 12 12"><rect x="1" y="1" width="10" height="10" fill="none" stroke="#fff" stroke-width="1.3"/><line x1="3" y1="5" x2="9" y2="5" stroke="#fff" stroke-width="1.3"/></svg></span>Social Feed Ads</div>
      <p>We will place targeted ads in the feeds of people that live in the surrounding area of your open house so they know there is a house for sale and come check it out.</p></div>
    <div class="service"><div class="service-head"><span class="service-icon"><svg width="10" height="14" viewBox="0 0 10 14"><rect x="3" y="1" width="4" height="8" rx="2" fill="none" stroke="#fff" stroke-width="1.3"/><path d="M1 7a4 4 0 0 0 8 0M5 11v2" fill="none" stroke="#fff" stroke-width="1.3"/></svg></span>Voice Broadcast</div>
      <p>We will send a voice broadcast to all the people that lived in the surrounding area of your open house so they know there is a house for sale and want to come check it out.</p></div>
  </div>
  <span class="btn-red">Contact us right now</span>
  <div class="agent-photo" role="img" aria-label="Photo of a smiling agent holding a red sold sign"></div>
</section>

<section class="section area">
  <div class="area-band"></div>
  <h2 class="section-title">Service Area</h2>
  <div class="search"><div class="search-input">Enter your open house address</div><div class="search-btn">Submit</div></div>
  <div class="map" role="img" aria-label="Map of the coastal service area with surrounding cities and ocean"></div>
  <div class="cta-row"><span class="btn-red">Contact us right now</span></div>
</section>

<section class="section faq">
  <h2 class="section-title">Frequently Asked Questions</h2>
  <div class="faq-cols">
    <div class="faq-col">
      <div class="faq-item"><span>How far ahead should I book my open house signs?</span><span>+</span></div>
      <div class="faq-item"><span>Do you pick up every sign after the event ends?</span><span>+</span></div>
      <div class="faq-item"><span>Can I bring my own branded signs to use?</span><span>+</span></div>
      <div class="faq-item"><span>Which areas do you currently cover?</span><span>+</span></div>
    </div>
    <div class="faq-col">
      <div class="faq-item"><span>How do the monthly subscription plans work?</span><span>+</span></div>
      <div class="faq-item open"><span>Can I combine signs with marketing services?</span><span>−</span></div>
      <div class="faq-answer">Yes. Any package can be paired with SMS, email, ad or voice campaigns, so nearby buyers hear about your open house before the day and your signs guide them right to the door.</div>
      <div class="faq-item"><span>What happens if a sign goes missing?</span><span>+</span></div>
      <div class="faq-item"><span>How do I pay for my booking?</span><span>+</span></div>
    </div>
  </div>
  <div class="cta-row"><span class="btn-red">Contact us right now</span></div>
</section>

<section class="section testimonials">
  <h2 class="section-title">Clients Testimonials</h2>
  <div class="quotes">
    <div class="quote"><span class="quote-mark l">“</span><span class="quote-mark r">”</span>
      <p>Their team set out every sign before sunrise and had them back in the truck by evening. My open house was packed, and I spent the morning with buyers instead of driving around with stakes and a hammer.</p>
      <div class="avatar" role="img" aria-label="Client portrait"></div><h4>Maren Holt</h4></div>
    <div class="quote-divider"></div>
    <div class="quote"><span class="quote-mark l">“</span><span class="quote-mark r">”</span>
      <p>The text and email campaign brought neighbors through the door who had never seen our listing online. Booking takes minutes, and the results have made this a regular part of every listing we run.</p>
      <div class="avatar" role="img" aria-label="Client portrait"></div><h4>Daniel Price</h4></div>
  </div>
  <div class="dots"><i></i><i></i><i></i><i class="on"></i><i></i></div>
  <div class="cta-row"><span class="btn-red">Contact us right now</span></div>
</section>

<footer class="section site-footer">
  <div class="ribbon">Subscribe to our newsletter</div>
  <div class="footer-cols">
    <div class="footer-col about"><h4>About TallyPorch Helpers</h4>
      <p>TallyPorchHelpers.net is operated by a local team that places signs and drives buyers to open houses, freeing agents to focus on clients and closing.</p>
      <div class="socials"><i></i><i></i><i></i><i></i><i></i></div></div>
    <div class="footer-col contact"><h4>Contact Information</h4>
      <p>410 Larkspur Row, Suite 12<br>Bayview, CA 90000</p>
      <p>1-555-014-2290</p>
      <p>E-mail Us:<br>hello@tallyporchhelpers.net</p></div>
    <div class="footer-col links"><h4>Quick Links</h4>
      <p>How It Works<br>Service Area<br>Pricing<br>About Us<br>FAQ</p></div>
    <div class="footer-col form"><h4>Contact Us Right Now</h4>
      <div class="field">Name</div><div class="field">Email</div><div class="field">Phone</div><div class="field">Message</div>
      <div class="send">Send a message</div></div>
  </div>
  <div class="bottom-bar"><span class="copy">Copyright © 2024 TallyPorch Helpers</span><span class="legal">Terms of Use | Privacy | Sitemap</span></div>
</footer>

</body>
</html>
```